ORLA - Óptica Médica - web design and concept

Website concept - Create and develop our website design and structure. ORLA is an optical store chain, and we are looking to establish our web and digital concept. In attachment there are several pictures about our stores and our logo.

The website structure should be user friendly. Colors should be light and the design as simple and minimalist as possible. There are different variations of the logothat can be used, check the file.

The website will include optical collections and sun collections as an online store. Also, a medical menu should be considered in order for clients to schedule optometry appointments. There should also be a menu for client assistance where the clients can read about glass maintenance in our workshop.
Updates

Low design quality

Number of Pages Required

5+ page

Font styles to use
Serif
Sans Serif

Requirements
Must have
• Must be user-friendly and minimalist.
• Please USE PICTURES FROM THE BRANDS we sell: MERUN, BOSKA, PNW, KOLE, BAMPE
Nice to have
• Nice to inspire: ZEK glasses (see website https://ch.shopzek.com/en/)
• Nice to inspire: https://merun-eyewear.com/
• Nice to ispire: https://www.pnwglobe.com/en/
Should not have
• Hysteric colors and shapes

```html
<!DOCTYPE html>
<html lang="en">
<head>
<meta charset="utf-8">
<title>ORLA Óptica Médica – Stores</title>
<link rel="stylesheet" href="https://fonts.googleapis.com/css2?family=Raleway:wght@300;400;500;600;700&display=swap">
<style>
:root{
  --accent:#f2a93b;
  --ink:#222;
  --muted:#777;
  --line:#e3e3e3;
  --soft:#f4f4f4;
  --footer:#0b0b0b;
  --white:#fff;
  --room-dark:#2a2722;
  --room-teal:#4f9ea0;
  --room-gold:#b99a5e;
}
*{box-sizing:border-box;margin:0;padding:0}
html,body{width:1200px;height:2840px;overflow:hidden;background:var(--white)}
body{font-family:"Raleway",sans-serif;color:var(--ink);position:relative}
a{color:inherit;text-decoration:none}

.topbar{position:absolute;top:0;left:0;width:1200px;height:96px}
.social{position:absolute;left:160px;top:14px;display:flex;gap:10px}
.social span{width:10px;height:10px;border-radius:50%;background:#333;display:block}
.brand{position:absolute;left:0;width:1200px;top:10px;text-align:center}
.brand .mark{font-size:30px;font-weight:600;letter-spacing:6px;color:var(--ink)}
.brand .sub{font-size:8px;letter-spacing:3px;color:var(--muted);display:block;margin-top:-2px}
.contact-top{position:absolute;right:160px;top:12px;display:flex;gap:16px;font-size:11px;color:#444;align-items:center}
.contact-top .tag{background:var(--accent);color:#fff;padding:2px 6px;font-size:10px}

.nav{position:absolute;top:100px;left:0;width:1200px;height:30px;display:flex;justify-content:center;align-items:center;gap:26px;font-size:11px;color:#444}
.nav .active{color:var(--accent)}
.nav .cta{background:var(--accent);color:#fff;padding:6px 12px;font-weight:600}
.rule{position:absolute;top:140px;left:0;width:1200px;height:1px;background:var(--line)}

.page-title{position:absolute;top:228px;width:1200px;text-align:center;font-size:58px;font-weight:300;letter-spacing:3px;color:#555}

.filters{position:absolute;top:396px;left:160px;width:880px;display:flex;gap:16px}
.filters div{flex:1;height:28px;border:1px solid var(--line);font-size:10px;color:var(--muted);display:flex;align-items:center;padding:0 10px}
.reset{position:absolute;top:448px;left:160px;font-size:10px;color:var(--muted)}

.store{position:absolute;width:280px}
.store .photo{width:280px;height:280px;background:linear-gradient(180deg,var(--room-dark) 0%,var(--room-gold) 45%,var(--room-teal) 70%,#d9d2c4 100%)}
.store .photo.light{background:linear-gradient(180deg,#c9c6c1 0%,#8e8a83 40%,#d7d2c8 100%)}
.store .info{font-size:10px;color:var(--muted);line-height:15px;margin-top:12px}
.store .info b{color:#444;font-weight:500}
.store .book{display:inline-block;background:var(--accent);color:#222;font-size:9px;font-weight:600;padding:4px 8px;margin-top:10px;letter-spacing:.5px}
.store .more{font-size:17px;color:#333;margin-top:12px}

.features{position:absolute;top:2004px;left:160px;width:880px;display:flex;gap:24px}
.feature{flex:1;height:88px;border:1px solid var(--line);display:flex;align-items:center;justify-content:center;gap:14px}
.feature svg{width:36px;height:36px}
.feature h4{font-size:16px;font-weight:500;color:#333}
.feature p{font-size:10px;color:var(--muted);margin-top:2px}

.brands{position:absolute;top:2140px;left:0;width:1200px;height:140px;background:var(--soft);display:flex;align-items:center;justify-content:center;gap:70px}
.brands .name{font-size:22px;font-weight:600;color:#222;letter-spacing:1px}
.brands .arrow{position:absolute;top:52px}
.brands .arrow.l{left:72px}.brands .arrow.r{right:72px}

.newsletter{position:absolute;top:2340px;width:1200px;text-align:center}
.newsletter h3{font-size:28px;font-weight:300;color:#444}
.newsletter .small{font-size:10px;color:var(--accent);margin-top:6px}
.signup{position:absolute;top:2404px;left:300px;width:600px;height:56px;border:1px solid var(--line);display:flex}
.signup span{flex:1;font-size:11px;color:var(--muted);display:flex;align-items:center;padding-left:16px}
.signup button{width:90px;border:0;background:var(--accent);display:flex;align-items:center;justify-content:center}

.footer{position:absolute;top:2532px;left:0;width:1200px;height:308px;background:var(--footer);color:#ccc}
.f-about{position:absolute;left:160px;top:44px;width:170px;font-size:10px;line-height:15px}
.f-about .mark{font-size:26px;font-weight:600;letter-spacing:5px;color:var(--accent);line-height:30px;margin-bottom:6px}
.f-about .more{color:#fff;font-weight:600;margin-top:8px;display:block}
.f-about .social{position:static;margin-top:10px}
.f-about .social span{background:var(--accent)}
.f-col{position:absolute;top:60px;font-size:10px;line-height:18px}
.f-col h5{color:var(--accent);font-size:11px;font-weight:700;letter-spacing:1px;margin-bottom:8px}
.f-col h5::after{content:"";display:block;width:40px;height:1px;background:#444;margin-top:4px}
.f-bottom{position:absolute;left:160px;right:160px;top:252px;border-top:1px solid #333;padding-top:14px;font-size:11px;display:flex;justify-content:space-between}
</style>
</head>
<body>

<header class="topbar">
  <div class="social"><span></span><span></span><span></span><span></span></div>
  <div class="brand"><span class="mark">ORLA</span><span class="sub">ÓPTICA MÉDICA</span></div>
  <div class="contact-top"><span class="tag">+351 210 000 000</span><span>info@orlaoptica.com</span></div>
</header>

<nav class="nav">
  <a>Home</a><a>Online Store</a><a>Company History</a><a>Medical Section</a><a class="active">Stores</a><a>Contact Us</a><a class="cta">Book an Appointment</a>
</nav>
<div class="rule"></div>

<h1 class="page-title">STORES</h1>

<div class="filters">
  <div>All Countries</div><div>All Cities</div><div>Choose Of Services</div><div>Near By</div>
</div>
<div class="reset">✕ Reset your filter</div>

<article class="store" style="left:160px;top:508px"><div class="photo" role="img" aria-label="Store interior with chandelier and teal display cases"></div><div class="info"><b>ORLA Óptica Médica</b><br>2800 Harbor Street<br>Lisbon 1100-000<br><br>Phone: +351 210 000 000</div><div class="more">More Information ...</div></article>
<article class="store" style="left:460px;top:508px"><div class="photo light" role="img" aria-label="Store interior with central counter"></div><div class="info"><b>ORLA Óptica Médica</b><br>2800 Harbor Street<br>Lisbon 1100-000<br><br>Phone: +351 210 000 000</div><span class="book">BOOK A CONSULT TEST</span><div class="more">More Information ...</div></article>
<article class="store" style="left:760px;top:508px"><div class="photo" role="img" aria-label="Store interior with eyewear displays"></div><div class="info"><b>ORLA Óptica Médica</b><br>2800 Harbor Street<br>Lisbon 1100-000<br><br>Phone: +351 210 000 000</div><span class="book">BOOK A CONSULT TEST</span><div class="more">More Information ...</div></article>

<article class="store" style="left:160px;top:988px"><div class="photo" role="img" aria-label="Store interior with chandelier and teal display cases"></div><div class="info"><b>ORLA Óptica Médica</b><br>2800 Harbor Street<br>Lisbon 1100-000<br><br>Phone: +351 210 000 000</div><span class="book">BOOK A CONSULT TEST</span><div class="more">More Information ...</div></article>
<article class="store" style="left:460px;top:988px"><div class="photo light" role="img" aria-label="Store interior with central counter"></div><div class="info"><b>ORLA Óptica Médica</b><br>2800 Harbor Street<br>Lisbon 1100-000<br><br>Phone: +351 210 000 000</div><span class="book">BOOK A CONSULT TEST</span><div class="more">More Information ...</div></article>
<article class="store" style="left:760px;top:988px"><div class="photo" role="img" aria-label="Store interior with eyewear displays"></div><div class="info"><b>ORLA Óptica Médica</b><br>2800 Harbor Street<br>Lisbon 1100-000<br><br>Phone: +351 210 000 000</div><span class="book">BOOK A CONSULT TEST</span><div class="more">More Information ...</div></article>

<article class="store" style="left:160px;top:1472px"><div class="photo" role="img" aria-label="Store interior with chandelier and teal display cases"></div><div class="info"><b>ORLA Óptica Médica</b><br>2800 Harbor Street<br>Lisbon 1100-000<br><br>Phone: +351 210 000 000</div><span class="book">BOOK A CONSULT TEST</span><div class="more">More Information ...</div></article>
<article class="store" style="left:460px;top:1472px"><div class="photo light" role="img" aria-label="Store interior with central counter"></div><div class="info"><b>ORLA Óptica Médica</b><br>2800 Harbor Street<br>Lisbon 1100-000<br><br>Phone: +351 210 000 000</div><span class="book">BOOK A CONSULT TEST</span><div class="more">More Information ...</div></article>
<article class="store" style="left:760px;top:1472px"><div class="photo" role="img" aria-label="Store interior with eyewear displays"></div><div class="info"><b>ORLA Óptica Médica</b><br>2800 Harbor Street<br>Lisbon 1100-000<br><br>Phone: +351 210 000 000</div><span class="book">BOOK A CONSULT TEST</span><div class="more">More Information ...</div></article>

<section class="features">
  <div class="feature">
    <svg viewBox="0 0 36 36" fill="none" stroke="#f2a93b" stroke-width="2"><rect x="3" y="10" width="18" height="13"/><path d="M21 14h7l5 5v4H21z"/><circle cx="10" cy="26" r="3"/><circle cx="27" cy="26" r="3"/></svg>
    <div><h4>Free Shipping</h4><p>On all orders above 50 euros</p></div>
  </div>
  <div class="feature">
    <svg viewBox="0 0 36 36" fill="none" stroke="#f2a93b" stroke-width="2"><path d="M7 20v-3a11 11 0 0 1 22 0v3"/><rect x="5" y="19" width="5" height="9"/><rect x="26" y="19" width="5" height="9"/></svg>
    <div><h4>Premium Support</h4><p>24/7 dedicated assistance</p></div>
  </div>
  <div class="feature">
    <svg viewBox="0 0 36 36" fill="none" stroke="#f2a93b" stroke-width="2"><rect x="4" y="9" width="28" height="19" rx="2"/><path d="M4 15h28"/></svg>
    <div><h4>Payment Method</h4><p>Cash on delivery</p></div>
  </div>
</section>

<section class="brands">
  <svg class="arrow l" width="20" height="36" viewBox="0 0 20 36" fill="none" stroke="#333" stroke-width="2"><path d="M17 2 3 18l14 16"/></svg>
  <span class="name">Norvane</span><span class="name">Tesmo</span><span class="name">Quillbrook</span><span class="name">Adrelle</span><span class="name">Vantori</span>
  <svg class="arrow r" width="20" height="36" viewBox="0 0 20 36" fill="none" stroke="#f2a93b" stroke-width="2"><path d="M3 2l14 16L3 34"/></svg>
</section>

<section class="newsletter">
  <h3>Subscribe For Our Newsletter</h3>
  <p class="small">Get news on new collections</p>
</section>
<div class="signup"><span>E-Mail Address</span><button aria-label="Send"><svg width="26" height="22" viewBox="0 0 26 22" fill="#222"><path d="M1 1l24 10L1 21l3-10z"/></svg></button></div>

<footer class="footer">
  <div class="f-about">
    <div class="mark">ORLA</div>
    <p>Curated eyewear and medical optometry care, offering quality lenses for every style and need.</p>
    <a class="more">READ MORE</a>
    <div class="social"><span></span><span></span><span></span><span></span></div>
  </div>
  <div class="f-col" style="left:420px"><h5>QUICK LINK</h5>Women<br>Men<br>Kids<br>Collections<br>Contact Us</div>
  <div class="f-col" style="left:630px"><h5>ACCOUNT</h5>My Account<br>Wishlist<br>Checkout<br>Create Account<br>Register</div>
  <div class="f-col" style="left:860px"><h5>QUICK CONTACT</h5>☏ +351 210 000 000<br>✉ info@orlaoptica.com<br>⌖ 2800 Harbor Street,<br>&nbsp;&nbsp;&nbsp;Lisbon 1100-000</div>
  <div class="f-bottom"><span>Copyright © 2018 ORLA Óptica Médica. All Rights Reserved.</span><span>Privacy Policy · Terms &amp; Conditions</span></div>
</footer>

</body>
</html>
```